Responsive Mobile Quelvo Jewelry Template

We need to adapt an existing Quelvo template to be 100% responsive and mobile friendly. Due to Quelvo rules, the template would need to be implemented only using HTML and CSS (no Javascript). The template design files and HTML/CSS files are required for this project. We prefer that it is implemented using a responsive framework such as Gridwell.

An example of our current template can be found here (diamond only):
https://www.quelvo-market.example/itm/507318829106?ViewItem=&item=507318829106

And example of our template with an additional section for gemstone:
https://www.quelvo-market.example/itm/507318826673?ViewItem=&item=507318826673

We had also somewhat recently designed our Quelvo store landing page so some consistency with this would be desired:
http://www.quelvoshops.example/MirrowCraftNV

Please also refer to our website: https://mirrowcraftnv.example/

Target Market(s)

Primarily women shopping for jewelry on Quelvo.

Industry/Entity Type

Jewelry

Coding

Coded - Design and coding required

Number of Pages Required

1 page

Font styles to use
Sans Serif

Requirements
Must have
• * A color scheme that fits with the existing template design.
• * REMOVE the product photo in the template.
• * Sections required for Description, Basic Details, and Diamond/Gemstone Details.
• * Please refer to https://pages.quelvo-market.example/sell/itemdescription/mobilefriendlyguidelines.html in particular, the template must use
Nice to have
• * Menu of links to other categories is desired in a mobile friendly way.
• * We are open to graphics for links to popular categories similar to those found on the store page.
• * Implemented using a standardized responsive framework such as Gridwell.

```html
<!DOCTYPE html>
<html lang="en">
<head>
<meta charset="utf-8">
<title>Mirrow Craft Nevada – Item Listing</title>
<link href="https://fonts.googleapis.com/css2?family=Roboto:ital,wght@0,400;0,500;0,700;1,700&display=swap" rel="stylesheet">
<style>
:root{
  --page:#f3f3f3;
  --sheet:#ffffff;
  --purple:#9985b8;
  --purple-text:#a48ec6;
  --lilac:#f2ecfb;
  --lilac-line:#dcd0ee;
  --ink:#3c3c3c;
  --ink-soft:#555;
  --line:#e2e2e2;
}
*{box-sizing:border-box;margin:0;padding:0}
html,body{width:825px;height:1200px;overflow:hidden}
body{background:var(--page);font-family:"Roboto",sans-serif;color:var(--ink);position:relative}
.sheet{position:absolute;left:78px;top:60px;width:670px;height:1080px;background:var(--sheet);border:1px solid var(--line)}
.topbar{height:18px;background:var(--purple);display:flex;justify-content:center;align-items:center;gap:8px;font-size:7px;color:#fff}
.topbar span.sep{opacity:.8}
.masthead{height:49px;background:linear-gradient(#e6dcf5,#fff);border-bottom:1px solid var(--line);display:flex;justify-content:center;align-items:center;gap:8px}
.brand-mark{width:10px;height:10px;border-radius:50%;background:var(--purple)}
.brand{text-align:center;color:var(--purple);font-size:15px;letter-spacing:1px;line-height:1}
.brand small{display:block;font-size:8px;letter-spacing:4px;margin-top:3px}
.section-title{position:absolute;top:102px;width:100%;text-align:center;font-size:12.5px;font-weight:700;font-style:italic;color:#222}
.categories{position:absolute;left:19px;top:140px;display:grid;grid-template-columns:repeat(5,121px);gap:6px 6.5px}
.cat{height:38px;border:1px solid #c9bfdb;display:flex;align-items:center;gap:7px;padding:0 6px;font-size:7px;color:var(--purple-text);text-transform:uppercase;line-height:1.5}
.cat-icon{flex:none;width:14px;height:14px;border:1.3px solid var(--purple);border-radius:50%}
.panel{position:absolute;top:259px;width:284px;height:266px;background:var(--lilac);border:1px solid var(--lilac-line)}
.panel h2{height:30px;background:var(--purple);color:#fff;font-size:13px;font-weight:500;padding-left:36px;line-height:30px}
.panel dl{display:grid;row-gap:13px;padding:21px 0 0 36px;font-size:9px;line-height:11px;color:var(--ink-soft)}
.panel .row{display:flex}
.panel dt{width:80px}
.panel.item{left:38px}
.panel.diamond{left:349px}
.panel.diamond h2,.panel.diamond dl{padding-left:26px}
.panel.diamond dt{width:122px}
.panel .note{padding:21px 0 0 26px;font-size:9.5px;font-weight:500;color:var(--purple-text)}
.tabs{position:absolute;left:39px;top:549px;width:593px;height:238px;border:1px solid var(--line)}
.tab-row{display:flex;height:30px;border-bottom:1px solid var(--line);font-size:9px;font-weight:500;color:var(--purple-text);align-items:center}
.tab{padding:0 17px}
.tab.active{background:var(--purple);color:#fff;height:30px;line-height:30px;width:146px;text-align:center;margin-right:17px}
.tab-body{padding:20px 14px 0;font-size:8.5px;color:var(--ink-soft);line-height:24px}
.tab-body .lead{line-height:16px}
.tab-body h3{font-size:9.5px;font-weight:500;color:#222;line-height:16px;margin:7px 0 4px}
.questions{position:absolute;left:39px;top:799px;width:593px;height:66px;border:1px solid var(--line)}
.questions h2{height:33px;background:var(--lilac);color:var(--purple-text);font-size:12.5px;font-weight:500;line-height:33px;padding-left:15px}
.questions p{font-size:8px;padding:11px 0 0 15px;display:flex;align-items:center;gap:9px}
.badges{position:absolute;left:39px;top:882px;display:flex;gap:12px}
.badge{height:62px;border:1px solid var(--line);background:#f6f6f6}
.badge.b1{width:85px}.badge.b2{width:101px}
.badge.b3{width:72px;height:66px;display:flex;align-items:center;justify-content:center;background:#fff}
.badge.b3 span{width:60px;height:60px;border-radius:50%;background:#6b84a3}
.footer{position:absolute;left:0;bottom:0;width:100%;height:60px;background:#f5f5f5;border-top:1px solid var(--line);padding:13px 0 0 26px;font-size:8px;color:#444}
.footer nav{display:flex;gap:6px}
.footer p{margin-top:10px;color:#555}
.footer p b{color:#111;font-weight:500}
</style>
</head>
<body>
<main class="sheet">
  <div class="topbar"><span>About Us</span><span class="sep">|</span><span>FAQs</span><span class="sep">|</span><span>Why Buy From Us</span><span class="sep">|</span><span>Save Seller</span></div>
  <header class="masthead">
    <span class="brand-mark"></span>
    <div class="brand">MIRROW CRAFT<small>NEVADA</small></div>
  </header>

  <h1 class="section-title">PLEASE CHOOSE A CATEGORY BELOW TO SEE MORE SUBCATEGORIES</h1>
  <nav class="categories">
    <a class="cat"><span class="cat-icon"></span>Diamond Engagement Rings</a>
    <a class="cat"><span class="cat-icon"></span>Fancy Yellow &amp; Pink Diamond</a>
    <a class="cat"><span class="cat-icon"></span>Cocktail Fashion Diamond Rings</a>
    <a class="cat"><span class="cat-icon"></span>Colored Gemstone Diamond Rings</a>
    <a class="cat"><span class="cat-icon"></span>Semi Mount Diamond Rings</a>
    <a class="cat"><span class="cat-icon"></span>Men's Diamond Jewelry</a>
    <a class="cat"><span class="cat-icon"></span>Diamond Pendants</a>
    <a class="cat"><span class="cat-icon"></span>Diamond Earrings</a>
    <a class="cat"><span class="cat-icon"></span>Diamond Necklaces</a>
    <a class="cat"><span class="cat-icon"></span>Diamond Bracelets &amp; Bangles</a>
  </nav>

  <section class="panel item">
    <h2>ITEM DETAILS</h2>
    <dl>
      <div class="row"><dt>Model Number :</dt><dd>MCN-RX52714BTD-480</dd></div>
      <div class="row"><dt>Metal :</dt><dd>14k Yellow Gold</dd></div>
      <div class="row"><dt>Weight :</dt><dd>4.08 grams</dd></div>
      <div class="row"><dt>L x W x H:</dt><dd>12 x 10 x 7.2 MM</dd></div>
      <div class="row"><dt>Style :</dt><dd>Halo</dd></div>
      <div class="row"><dt>Ring Size :</dt><dd>6 (contact us for sizing options)</dd></div>
    </dl>
  </section>

  <section class="panel diamond">
    <h2>DIAMOND DETAILS</h2>
    <dl>
      <div class="row"><dt>Total Carat Weight :</dt><dd>0.19 CT</dd></div>
      <div class="row"><dt>Diamond Count :</dt><dd>22</dd></div>
      <div class="row"><dt>Shape :</dt><dd>Round</dd></div>
      <div class="row"><dt>Color/Clarity :</dt><dd>G / SI1</dd></div>
      <div class="row"><dt>Other Shape :</dt><dd>Round</dd></div>
      <div class="row"><dt>Other Color/Clarity :</dt><dd>G / SI1</dd></div>
      <div class="row"><dt>Certificate :</dt><dd>VCL (click for more info)</dd></div>
    </dl>
    <p class="note">All of our diamonds and gemstones are 100% natural!</p>
  </section>

  <section class="tabs">
    <div class="tab-row">
      <span class="tab active">SHIPPING DETAILS</span>
      <span class="tab">PRODUCT GUARANTEE</span>
      <span class="tab">RETURN POLICY</span>
      <span class="tab">PRIVACY POLICY</span>
      <span class="tab">WHY US</span>
    </div>
    <div class="tab-body">
      <p class="lead">Parcelo 2 Day: Free (U.S.A. only)</p>
      <h3>WE SHIP WORLDWIDE</h3>
      <p>International Buyers - Please Note: Import duties, taxes, and charges are not included in the item price or shipping cost. These charges are the</p>
      <p>buyer's responsibility. Please check with your country's customs office to determine what these additional costs will be prior to bidding or buying.</p>
      <p>All packages are fully insured and require signature confirmation.</p>
      <p>Once your item(s) are ready to leave our facility a shipping tracking number will be sent to you. Business days do not include Saturday, Sunday or</p>
      <p>holidays. Please be sure to inspect your package upon arrival for tampering or any damage. Rush orders are welcome. Please call for availability.</p>
    </div>
  </section>

  <section class="questions">
    <h2>Questions?</h2>
    <p><svg width="9" height="7" viewBox="0 0 9 7"><rect x=".5" y=".5" width="8" height="6" fill="none" stroke="#9985b8"/><path d="M.5 .5 4.5 4 8.5 .5" fill="none" stroke="#9985b8"/></svg>Ask a question via email</p>
  </section>

  <div class="badges">
    <div class="badge b1" role="img" aria-label="Accreditation badge"></div>
    <div class="badge b2" role="img" aria-label="Gem institute badge"></div>
    <div class="badge b3" role="img" aria-label="Gem laboratory badge"><span></span></div>
  </div>

  <footer class="footer">
    <nav><span>About Quelvo</span>|<span>Announcements</span>|<span>Community</span>|<span>Security Center</span>|<span>Resolution Center</span>|<span>Seller Center</span>|<span>Policies</span>|<span>Affiliates</span>|<span>Help &amp; Contact</span>|<span>Site Map</span></nav>
    <p><b>Copyright © 1995-2018 Quelvo Inc. All Rights Reserved.</b> Accessibility, User Agreement, Privacy, Cookies and AdChoice</p>
  </footer>
</main>
</body>
</html>
```